Business Card and Letterhead for Pimlu - modern real estate business

I need a double sided business card design for Pimlu. Please see business card brief here https://files.trelvonadocs.com/sheet/r/7QzTmWbaXLJnoPEd-kRyUgFhHsstbvCe2qfoMxDa_pz/view?mode=shared

Please feel free to design the business cards however you feel best. I am happy to give some creative freedoms and then provide feedback from there.

Please then also create a letterhead to match the business card design

Colors

Designer to choose colors to be used in the design.

Requirements
Must have
• Must be a modern, elegant business card which looks very professional

```html
<!DOCTYPE html>
<html lang="en">
<head>
<meta charset="utf-8">
<title>Pimlu Letterhead</title>
<link href="https://fonts.googleapis.com/css2?family=Montserrat:wght@400;500;700&family=Open+Sans:wght@400&display=swap" rel="stylesheet">
<style>
  :root {
    --backdrop: #a6b8bd;
    --paper: #ffffff;
    --brand-red: #e3101b;
    --ink: #2b2b2b;
    --body-ink: #4a4a4a;
    --signature-tone: #e6e6e9;
  }
  * { margin: 0; padding: 0; box-sizing: border-box; }
  html, body {
    width: 1200px;
    height: 907px;
    overflow: hidden;
    background: var(--backdrop);
  }
  .letterhead {
    position: absolute;
    left: 280px;
    top: 44px;
    width: 641px;
    height: 817px;
    background: var(--paper);
    box-shadow: 0 1px 4px rgba(0, 0, 0, 0.18);
    font-family: "Open Sans", Arial, sans-serif;
    color: var(--body-ink);
  }
  .brand-name {
    position: absolute;
    left: 50px;
    top: 40px;
    font-family: "Montserrat", Arial, sans-serif;
    font-weight: 700;
    font-size: 37px;
    letter-spacing: 0.5px;
    color: var(--brand-red);
    text-transform: uppercase;
  }
  .company-details {
    position: absolute;
    left: 493px;
    top: 25px;
    font-family: "Montserrat", Arial, sans-serif;
    font-size: 10px;
    line-height: 12px;
    color: var(--ink);
  }
  .registration { margin-bottom: 6px; }
  .contact-list { list-style: none; }
  .contact-list li {
    display: flex;
    align-items: center;
    gap: 5px;
    height: 12px;
  }
  .contact-icon { width: 8px; height: 8px; flex: none; }
  .letter-date {
    position: absolute;
    left: 69px;
    top: 228px;
    font-size: 10px;
    color: var(--ink);
  }
  .letter-body {
    position: absolute;
    left: 69px;
    top: 278px;
    width: 518px;
    font-size: 10px;
    line-height: 22.5px;
  }
  .letter-body p { margin-bottom: 3px; }
  .signature-mark {
    position: absolute;
    left: 440px;
    top: 576px;
    width: 132px;
    height: 42px;
    background: linear-gradient(90deg, var(--signature-tone), #f4f4f6);
    border-radius: 4px;
  }
  .signatory {
    position: absolute;
    left: 446px;
    top: 620px;
    font-size: 10px;
    line-height: 12px;
    color: var(--ink);
  }
  .postal-address {
    position: absolute;
    left: 0;
    width: 100%;
    top: 793px;
    text-align: center;
    font-family: "Montserrat", Arial, sans-serif;
    font-size: 10px;
    color: var(--ink);
  }
  .footer-band {
    position: absolute;
    left: 0;
    bottom: 0;
    width: 100%;
    height: 6px;
    background: var(--brand-red);
  }
</style>
</head>
<body>
  <article class="letterhead">
    <header>
      <div class="brand-name">Pimlu</div>
      <div class="company-details">
        <div class="registration">ABN: 48 219 706 335<br>Lic No. 20417683</div>
        <ul class="contact-list">
          <li>
            <svg class="contact-icon" viewBox="0 0 10 10" aria-hidden="true">
              <circle cx="5" cy="5" r="5" fill="#e3101b"/>
              <path d="M3.2 2.6 L4.2 2.4 L4.7 3.8 L4.1 4.3 Q4.6 5.5 5.7 5.9 L6.2 5.3 L7.6 5.8 L7.4 6.8 Q5.6 7.4 4 5.9 Q2.7 4.4 3.2 2.6 Z" fill="#fff"/>
            </svg>
            <span>02 4816 3907</span>
          </li>
          <li>
            <svg class="contact-icon" viewBox="0 0 10 10" aria-hidden="true">
              <circle cx="5" cy="5" r="5" fill="#e3101b"/>
              <rect x="2.6" y="3.3" width="4.8" height="3.4" fill="none" stroke="#fff" stroke-width="0.8"/>
              <path d="M2.6 3.3 L5 5.2 L7.4 3.3" fill="none" stroke="#fff" stroke-width="0.8"/>
            </svg>
            <span>info@pimlu.com</span>
          </li>
          <li>
            <svg class="contact-icon" viewBox="0 0 10 10" aria-hidden="true">
              <circle cx="5" cy="5" r="5" fill="#e3101b"/>
              <circle cx="5" cy="5" r="2.5" fill="none" stroke="#fff" stroke-width="0.7"/>
              <path d="M2.5 5 H7.5 M5 2.5 V7.5" stroke="#fff" stroke-width="0.6"/>
            </svg>
            <span>www.pimlu.com</span>
          </li>
        </ul>
      </div>
    </header>

    <p class="letter-date">Date, 10 September, 2020</p>

    <section class="letter-body">
      <p>This is a sample letter that has been placed to demonstrate typing remat (Your Company). letterhead design. When positioned properly, it will serve to work in harmony with all other elements letterhead. This letterhead design is meant to project an image</p>
      <p>This letterhead design is meant project an image of professionalism reliability. By using simple aligen we have created a very spacious feeling. The simplicity suggest rengththe spaciousnes contributes h aesthetics the layout. These basic qualities along with the (Your Company)</p>
      <p>look and helps reinforce the (Your Company) brand. letterhead design is meant to project an image p design. When positioned properly, it will serve to work in harmony all the other elements letterhead. sionalism and reliability.</p>
      <p>This letterhead design is based on the (Form of your logo) form (Your Company) logo. Each stationery we have created a very spacious feeling. The simplicity suggests strength the spaciousnes contribute part of the (Form of your logo).</p>
    </section>

    <div class="signature-mark" role="img" aria-label="Handwritten signature of Liam Carter"></div>
    <p class="signatory">Liam Carter<br>Manager</p>

    <footer>
      <p class="postal-address">PO Box 3172, Kelmora NSW 2790</p>
      <div class="footer-band"></div>
    </footer>
  </article>
</body>
</html>
```